Marcus Delbridge Finance

Need a personal website advertising Equipment Finance,Business Finance,Commercial Finance, Construction Finance, Bridging Finance. Similar websites are www.corvalend.com.au / www.tarmivest.com.au / www.qbr7.com.au /wwwhalvecredit.com.au

Target Market(s)

Business People

Industry/Entity Type

Business

Number of Pages Required

3 page

Font styles to use
Serif
Sans Serif

Requirements
Must have
• All i want is a simple corporate looking website advertising Equipment Finance, Commercial Finance, Construction Finance, Business Finance, Bridging Finance,

```html
<!DOCTYPE html>
<html lang="en">
<head>
<meta charset="utf-8">
<title>Marcus Delbridge Finance – Contact Us</title>
<link rel="stylesheet" href="https://fonts.googleapis.com/css2?family=Montserrat:wght@300;400;500;700&family=Roboto+Condensed:wght@700&family=Roboto:wght@400&display=swap">
<style>
:root{
  --top-bar:#0a7db0;
  --nav:#115f80;
  --nav-active:#39b7e0;
  --text-blue:#1c6a8e;
  --panel-head:#5288a0;
  --panel-body:#185e80;
  --cta:#f39c12;
  --cta-border:#f7b54a;
  --quote:#2aaee0;
  --search:#e6e6e6;
  --rule:#165e7f;
  --ink:#222;
  --grey:#bdbdbd;
  --light-line:#e8e8e8;
}
*{margin:0;padding:0;box-sizing:border-box}
html,body{width:1200px;height:1162px;overflow:hidden;background:#fff}
body{position:relative;font-family:"Montserrat",Arial,sans-serif;font-weight:300;color:var(--ink)}
.abs{position:absolute}
.top-bar{left:0;top:0;width:1200px;height:40px;background:var(--top-bar);color:#fff;font-size:12px;font-weight:400}
.top-bar .links{left:96px;top:13px}
.top-bar .phone{left:630px;top:13px}
.social-top{left:1016px;top:9px;display:flex;gap:3px}
.social-top span{width:18px;height:18px;border-radius:50%;background:#fff;display:block}
.brand{left:96px;top:66px;display:flex;align-items:center;gap:14px;font-size:31px;font-weight:400;color:#111}
.brand .dot{width:34px;height:34px;border-radius:50%;background:#111}
.search{left:624px;top:59px;width:310px;height:43px;background:var(--search);border-radius:3px}
.search svg{position:absolute;right:14px;top:11px}
.quote-btn{left:948px;top:59px;width:148px;height:43px;background:var(--quote);color:#fff;font-size:17px;font-weight:300;display:flex;align-items:center;justify-content:center;border-radius:2px}
.main-nav{left:0;top:125px;width:1200px;height:51px;background:var(--nav);display:flex;padding-left:96px}
.main-nav a{width:142px;height:51px;display:flex;align-items:center;justify-content:center;color:#fff;text-decoration:none;font-size:16px;font-weight:300;border-right:1px solid #fff}
.main-nav a:first-child{width:142px}
.main-nav a:last-child{border-right:none}
.main-nav a.active{color:var(--nav-active)}
.call-line{left:0;top:220px;width:1200px;display:flex;justify-content:center;align-items:center;gap:20px;color:var(--text-blue);font-size:24px;font-weight:300}
.office-photo{left:97px;width:342px;height:97px}
.photo-meeting{top:315px;background:linear-gradient(180deg,#9aa39b 0%,#c8a26e 55%,#8d6b45 100%)}
.photo-desk{top:595px;background:linear-gradient(90deg,#c7d6d8 0%,#d8b9a0 50%,#9a7a5a 100%)}
.office-details{left:96px;color:var(--text-blue);font-size:14px;line-height:24px;font-weight:300}
.consult{left:575px;top:312px;width:522px;height:524px;background:var(--panel-body)}
.consult-head{height:73px;background:var(--panel-head);color:#fff;font-weight:700;font-size:18px;display:flex;align-items:center;justify-content:center;letter-spacing:.3px}
.book-art{position:absolute;left:145px;top:93px;width:222px;height:236px;background:linear-gradient(160deg,#e8f0f4 0%,#b9d2de 60%,#6e9db4 100%)}
.field{position:absolute;left:93px;width:330px;height:45px;background:#fff;font-family:"Roboto",Arial,sans-serif;font-size:14px;color:#777;padding-left:15px;display:flex;align-items:center}
.cta{position:absolute;left:93px;top:451px;width:330px;height:50px;background:var(--cta);border:2px solid var(--cta-border);color:#fff;font-family:"Roboto Condensed",Arial,sans-serif;font-weight:700;font-size:17px;display:flex;align-items:center;justify-content:center}
.rule{left:96px;top:853px;width:1001px;height:4px;background:var(--rule)}
.footer-label{left:95px;top:906px;font-size:12px;font-weight:400}
.payments{left:97px;top:943px;width:154px;height:39px;border:1px solid #ddd;display:flex;align-items:center;gap:6px;padding-left:10px}
.payments span{width:24px;height:16px;border-radius:2px;background:#8aa2c8}
.payments span:nth-child(2){background:#f0a040}
.payments span:nth-child(3){background:#5b9bd5}
.payments span:nth-child(4){background:#c9d3df}
.info-row{left:312px;display:flex;gap:14px;font-size:12px;line-height:16px;font-weight:400}
.footer-links{right:103px;font-size:12px;font-weight:400;display:flex;gap:18px}
.footer-links .muted{color:#999}
.divider{left:0;top:1046px;width:1200px;height:1px;background:var(--light-line)}
.legal{left:96px;top:1074px;font-size:12px;line-height:24px;font-weight:400}
.follow{left:911px;top:1078px;display:flex;align-items:center;gap:10px;font-size:12px;font-weight:400}
.follow .circles{display:flex;gap:5px;margin-left:8px}
.follow .circles span{width:24px;height:24px;border-radius:50%;background:var(--grey)}
</style>
</head>
<body>

<div class="abs top-bar">
  <span class="abs links">E-Book - Downloads Sitemap</span>
  <span class="abs phone">T: 1000 000 000</span>
  <div class="abs social-top"><span></span><span></span><span></span><span></span></div>
</div>

<div class="abs brand"><span class="dot"></span>Marcus Delbridge Finance</div>
<div class="abs search">
  <svg width="22" height="22" viewBox="0 0 22 22"><rect width="22" height="22" rx="4" fill="#2aaee0"/><circle cx="10" cy="10" r="5" fill="none" stroke="#fff" stroke-width="2"/><line x1="14" y1="14" x2="17" y2="17" stroke="#fff" stroke-width="2.4" stroke-linecap="round"/></svg>
</div>
<div class="abs quote-btn">Quote Now</div>

<nav class="abs main-nav">
  <a href="#">Home</a>
  <a href="#">The Business</a>
  <a href="#">Key People</a>
  <a href="#">Products</a>
  <a href="#">Investors</a>
  <a href="#" class="active">Contact Us</a>
  <a href="#">Privacy</a>
</nav>

<div class="abs call-line">
  <svg width="22" height="28" viewBox="0 0 22 28"><path d="M6 1 L10 7 L7 10 C8 15 10 18 13 21 L16 18 L21 23 L17 27 C9 25 3 16 2 5 Z" fill="#1c6a8e"/></svg>
  <span>Speak with a specialist today toll free on 1000 000 000</span>
</div>

<div class="abs office-photo photo-meeting" role="img" aria-label="Photo of a boardroom table with office chairs"></div>
<div class="abs office-details" style="top:429px">
  Marcus Delbridge Finance Office<br>
  Phone: 1000 000 000<br>
  Email: applications@Marcus Delbridge Finance.au<br>
  Unit 8 The Arbour Centre<br>
  17 Calloway Road, MERRIDALE, QLD 4219
</div>

<div class="abs office-photo photo-desk" role="img" aria-label="Photo of hands typing on a laptop beside a cup of coffee"></div>
<div class="abs office-details" style="top:717px">
  Sydney Office<br>
  Phone: 1000 000 000<br>
  Email: applications@tarmivest.com.au<br>
  Level 12, 90 Harlow Street<br>
  Sydney, NSW 2000 Australia
</div>

<section class="abs consult">
  <div class="consult-head">GET FREE CONSULATION</div>
  <div class="book-art" role="img" aria-label="Illustration of the free finance toolkit e-book cover"></div>
  <div class="field" style="top:341px">Please enter your name</div>
  <div class="field" style="top:396px">Email Address</div>
  <div class="cta">SEND ME THE FREE TOOLKIT</div>
</section>

<div class="abs rule"></div>

<div class="abs footer-label">Payments</div>
<div class="abs payments"><span></span><span></span><span></span><span></span></div>

<div class="abs info-row" style="top:909px">
  <svg width="22" height="22" viewBox="0 0 22 22"><path d="M11 2 C7 2 5 5 5 8 C5 12 11 20 11 20 C11 20 17 12 17 8 C17 5 15 2 11 2 Z" fill="#111"/><circle cx="11" cy="8" r="2.3" fill="#fff"/></svg>
  <div>640 Brenmoor Drive,<br>Kelvin Shore, Queensland, 4210</div>
</div>
<div class="abs info-row" style="top:957px">
  <svg width="22" height="22" viewBox="0 0 22 22"><circle cx="11" cy="12" r="9" fill="none" stroke="#111" stroke-width="2"/><path d="M11 7 V12 H15" fill="none" stroke="#111" stroke-width="2"/></svg>
  <div>Mon – Fri 9:00am – 5:00pm<br>Sat – Sun - Closed</div>
</div>

<div class="abs footer-links" style="top:910px">
  <span class="muted">Home</span><span>The Business</span><span>Key People</span><span>Products</span><span>Investors</span><span>Contact Us</span><span>Privacy</span>
</div>
<div class="abs footer-links" style="top:939px;gap:8px">
  <span>E-Book | Downloads Sitemap</span><span>|</span><span>Privacy Policy</span><span>| Sitemap</span>
</div>

<div class="abs divider"></div>

<div class="abs legal">Secured by SSL<br>© 2017 Marcus Delbridge Finance</div>
<div class="abs follow">Follow Us<div class="circles"><span></span><span></span><span></span><span></span></div></div>

</body>
</html>
```